Design Brief for Website Redesign

Client Name: Harbourline IT
Website: www.harbourlineit.com.au
Industry: Managed IT Services
Target Audience: Small to medium-sized businesses in Australia, requiring IT solutions, IT support, cloud services, and phone systems.

Project Overview
We are seeking a full redesign of the Harbourline IT website to modernize its look, improve usability, and enhance user experience across devices. The goal is to create a professional, clean, and user-friendly website that reflects our expertise in IT services and appeals to our business clients.

Objectives
Modern Visual Identity: Create a fresh, modern design that aligns with Harbourline IT's branding.

Improved User Experience: Simplify navigation, improve accessibility, and enhance mobile responsiveness.

Clear Calls to Action: Ensure CTAs are prominent and encourage user engagement.

Enhanced Trust & Credibility: Highlight testimonials, case studies, and industry credentials.

SEO Optimization: Ensure the site is optimized for search engines, including proper heading structures and metadata.
Design Style & Tone
Professional: Clean, modern, and polished to reflect our IT expertise.

Minimalist: Simple layouts, plenty of white space, and easy-to-read typography.

Tech-focused: Subtle tech-themed design elements that reinforce our brand as a leading IT service provider.

Colors: Use our existing brand colors, or propose a color scheme that complements the tech industry while maintaining a professional feel.

Typography: Clear, readable fonts that convey professionalism and trustworthiness.

Key Pages & Features
Home Page:

Hero section with a clear value proposition.

Highlight key services (IT support, cloud solutions, phone systems, etc.) with icons and brief descriptions.

Prominent CTAs (e.g., “Request a Quote,” “Book a Demo”).

Testimonials from satisfied clients.

Services Page:

Detailed breakdown of the services we offer (IT support, cloud services, phone systems, etc.).

Use of icons or illustrations to make the services visually engaging.

Clear CTAs to request quotes or book consultations.

About Us Page:

Information about our company history, mission, and team.

Highlight our certifications, partnerships, and industry expertise.

Case Studies/Testimonials Page:

Showcase client success stories and testimonials with visuals and brief case study summaries.

Include a trust-building section with logos of major clients or partners.

Contact Page:

Simple contact form for inquiries.

Integrated map with office location.

Social media links and phone number.

Blog/Resource Section:

Easy-to-navigate blog section for IT-related articles, tips, and industry news.

Clear categorization and tags for easy browsing.

Knowledge Base/Support Page:

Self-service area for clients to find articles, FAQs, and support guides.

Option to submit a support ticket.

Mobile Responsiveness:

Ensure the design is fully responsive, with no horizontal scrolling or misaligned content on mobile.

Functional Requirements
Fast Load Times: Optimize images, minimize unnecessary scripts, and ensure the site loads quickly on both desktop and mobile.

User-Friendly CMS: We need a CMS that is easy to update (preferably WordPress, but open to other suggestions).

SEO Best Practices: Structure the site with proper metadata, alt tags, and semantic HTML for better search engine optimization.

Security: Ensure the website follows security best practices (SSL, HTTPS).

Deliverables
Full website design (desktop and mobile versions).

Design mockups in Photoshop, Sketch, or Figma (whichever is preferred).

Working prototype (optional).

Final website files, including images and assets.

A style guide for ongoing consistency.

Industry/Entity Type

IT Managed Services

Number of Pages Required

3 page

Requirements
Must have
• EXCELLENT UX/UI

```html
<!DOCTYPE html>
<html lang="en">
<head>
<meta charset="utf-8">
<title>Harbourline IT — Technology Solutions for a Better Business</title>
<link rel="stylesheet" href="https://fonts.googleapis.com/css2?family=Outfit:wght@400;500;600;700&family=Lato:wght@400;700&display=swap">
<style>
:root{
  --red:#e31b3c;
  --ink:#111111;
  --text:#2b2b2b;
  --white:#ffffff;
  --blush:#fdf3f4;
  --footer:#0c0c0d;
  --muted:#d9d9d9;
}
*{box-sizing:border-box;margin:0;padding:0}
html,body{width:1200px;height:2425px;overflow:hidden;background:var(--white)}
body{position:relative;font-family:"Lato",sans-serif;color:var(--text)}
.abs{position:absolute}
.brand{font-family:"Outfit",sans-serif;font-weight:700;color:var(--red);letter-spacing:-0.5px;white-space:nowrap}
.brand-header{left:111px;top:22px;font-size:34px;line-height:42px}
.brand-footer{left:111px;top:2094px;font-size:40px;line-height:50px}

/* header */
.site-header{left:0;top:0;width:1200px;height:86px;background:var(--white)}
.main-nav{left:386px;top:34px;font-family:"Outfit",sans-serif;font-size:14px;font-weight:500;color:var(--ink)}
.main-nav a{position:absolute;white-space:nowrap;color:inherit;text-decoration:none}
.main-nav a.active{color:var(--red)}
.quote-btn{left:1023px;top:0;width:177px;height:86px;background:var(--red);color:var(--white);font-family:"Outfit",sans-serif;font-weight:700;font-size:18px;display:flex;align-items:center;justify-content:center}

/* hero */
.hero{left:0;top:86px;width:1200px;height:548px;background:linear-gradient(100deg,#2b1f1c 0%,#3b3430 28%,#2e5f9c 48%,#6d8fb6 58%,#8a4a3a 72%,#b5725a 86%,#5a3226 100%)}
.hero-shade{left:0;top:86px;width:700px;height:548px;background:linear-gradient(90deg,rgba(0,0,0,.55),rgba(0,0,0,0))}
.hero-title{left:110px;top:186px;width:480px;font-family:"Outfit",sans-serif;font-weight:600;font-size:38px;line-height:50px;color:var(--white)}
.hero-copy{left:111px;top:345px;width:420px;font-weight:700;font-size:15px;line-height:28px;color:var(--white)}
.btn{height:42px;border-radius:4px;font-family:"Outfit",sans-serif;font-weight:600;font-size:14px;display:flex;align-items:center;justify-content:center}
.btn-solid{left:111px;top:446px;width:171px;background:var(--red);color:var(--white)}
.btn-light{left:300px;top:446px;width:208px;background:var(--white);color:var(--red)}
.scroll-notch{left:550px;top:590px;width:120px;height:45px}

/* services */
.section-title{left:0;width:1200px;text-align:center;font-family:"Outfit",sans-serif;font-weight:500;font-size:41px;color:var(--ink)}
.section-title b{color:var(--red);font-weight:700}
.svc-card{width:476px;height:321px;border-radius:14px;overflow:hidden}
.svc-label{left:0;bottom:0;width:100%;height:52px;background:linear-gradient(90deg,rgba(227,27,60,.95) 0%,rgba(227,27,60,.75) 45%,rgba(227,27,60,0) 75%);color:var(--white);font-family:"Outfit",sans-serif;font-weight:500;font-size:19px;padding:14px 0 0 23px}
.svc-label.open{height:104px;background:linear-gradient(90deg,rgba(227,27,60,.97) 0%,rgba(227,27,60,.9) 60%,rgba(227,27,60,.6) 100%);padding:15px 0 0 16px}
.svc-label.open p{font-family:"Lato",sans-serif;font-size:13px;line-height:21px;margin-top:11px;width:400px}

/* testimonials */
.reviews{left:0;top:1567px;width:1200px;height:456px;background:var(--blush)}
.review-card{top:1747px;width:300px;height:194px;background:var(--white);border-radius:6px;text-align:center;padding-top:53px}
.review-card h3{font-family:"Lato",sans-serif;font-weight:700;font-size:17px;color:var(--ink)}
.review-card .stars{color:#f2a81d;font-size:11px;letter-spacing:1px;margin-top:4px}
.review-card p{font-size:13.5px;line-height:26px;margin:3px 22px 0;color:#333}
.avatar{top:1711px;width:78px;height:78px;border-radius:50%;background:var(--white);padding:6px}
.avatar span{display:block;width:100%;height:100%;border-radius:50%}

/* footer */
.site-footer{left:0;top:2023px;width:1200px;height:402px;background:var(--footer)}
.social{top:2204px;width:28px;height:28px;border-radius:50%;border:1.5px solid var(--white)}
.foot-col h4{font-family:"Outfit",sans-serif;font-weight:500;font-size:19px;color:var(--white)}
.foot-col ul{list-style:none;margin-top:16px}
.foot-col li{display:flex;align-items:center;gap:9px;color:var(--white);font-size:15px;height:34px}
.contact-row{display:flex;align-items:center;gap:12px;color:var(--white);font-size:15px;line-height:27px}
.contact-row .ic{width:32px;height:32px;border-radius:50%;background:var(--white);display:flex;align-items:center;justify-content:center;flex:none}
.rule{left:111px;top:2343px;width:978px;height:1px;background:#3a3a3a}
.copyright{left:0;top:2394px;width:1200px;text-align:center;font-family:"Outfit",sans-serif;font-size:14px;color:var(--white)}
</style>
</head>
<body>

<header class="abs site-header">
  <div class="abs brand brand-header">Harbourline IT</div>
  <nav class="abs main-nav">
    <a class="active" style="left:0">HOME</a>
    <a style="left:80px">ABOUT</a>
    <a style="left:165px">SERVICES</a>
    <a style="left:268px">KNOWLEDGE BASE/SUPPORT</a>
    <a style="left:508px">CONTACT</a>
  </nav>
  <div class="abs quote-btn">GET A QUOTE</div>
</header>

<section>
  <div class="abs hero" role="img" aria-label="Upward view of city office towers against a blue sky"></div>
  <div class="abs hero-shade"></div>
  <h1 class="abs hero-title">TECHNOLOGY<br>SOLUTIONS FOR A<br>BETTER BUSINESS</h1>
  <p class="abs hero-copy">We understand that technology is a critical component of running a successful business, and that's why we're here to help you navigate the ever-changing landscape of IT.</p>
  <div class="abs btn btn-solid">REQUEST QUOTES</div>
  <div class="abs btn btn-light">BOOK CONSULTATIONS</div>
  <svg class="abs scroll-notch" viewBox="0 0 120 45">
    <path d="M0 45 C25 45 35 4 60 4 C85 4 95 45 120 45 Z" fill="#fff"/>
    <rect x="50" y="17" width="20" height="34" rx="10" fill="#9a9a9a"/>
    <path d="M60 24 V38 M55 33 L60 38 L65 33" stroke="#fff" stroke-width="1.6" fill="none" stroke-linecap="round"/>
  </svg>
</section>

<section>
  <h2 class="abs section-title" style="top:720px">OUR <b>SERVICES</b></h2>

  <div class="abs svc-card" style="left:118px;top:812px;background:linear-gradient(120deg,#0b1c3a,#173566 45%,#2b3e5e 70%,#5a4a2a)" role="img" aria-label="IT engineer working on a laptop beside server racks">
    <div class="abs svc-label">IT SOLUTIONS</div>
  </div>
  <div class="abs svc-card" style="left:607px;top:812px;background:linear-gradient(120deg,#e8ebec,#cfd6d4 45%,#d9b5a6 75%,#c99a88)" role="img" aria-label="Support agent wearing a headset at a desk">
    <div class="abs svc-label">IT SUPPORT</div>
  </div>
  <div class="abs svc-card" style="left:118px;top:1146px;background:radial-gradient(circle at 60% 50%,#6f9fd6 0%,#1c3558 30%,#0a0f1a 70%)" role="img" aria-label="Hand holding a glowing cloud network symbol">
    <div class="abs svc-label">CLOUD SERVICES</div>
  </div>
  <div class="abs svc-card" style="left:607px;top:1146px;background:linear-gradient(120deg,#16335e,#2c5a93 45%,#4a6fa3 70%,#1d3b68)" role="img" aria-label="Professional working at screens filled with code">
    <div class="abs svc-label open">
      <div style="display:flex;align-items:center;gap:18px;font-size:19px">PHONE SYSTEMS
        <svg width="30" height="28" viewBox="0 0 30 28"><rect x="9" y="1" width="18" height="20" rx="2" fill="none" stroke="#fff" stroke-width="1.6"/><path d="M13 7h10M13 11h10" stroke="#fff" stroke-width="1.4"/><path d="M4 14c0 6 5 11 11 11l2-3-3-3-2 1c-2-1-3-2-4-4l1-2-3-3z" fill="#fff"/></svg>
      </div>
      <p>Excepteur sint occaecat cupidatat non proident, sunt in culpa qui officia deserunt mollit anim id est laborum.</p>
    </div>
  </div>
</section>

<section>
  <div class="abs reviews"></div>
  <h2 class="abs section-title" style="top:1627px">WHAT OUR <b>CUSTOMER SAYS</b></h2>

  <div class="abs review-card" style="left:111px"><h3>Daniel Marsh</h3><div class="stars">★★★★★</div><p>Temporibus autem quibusdam et aut officiis debitis aut rerum necessitatibus saepe eveniet ut et voluptates</p></div>
  <div class="abs review-card" style="left:450px"><h3>Oliver Grant</h3><div class="stars">★★★★★</div><p>Itaque earum rerum hic tenetur a sapiente delectus, reiciendis voluptatibus maiores alias consequatur aut</p></div>
  <div class="abs review-card" style="left:789px"><h3>Chloe Bennett</h3><div class="stars">★★★★★</div><p>Nam libero tempore, cum soluta nobis est eligendi optio cumque nihil impedit quo minus id quod</p></div>

  <div class="abs avatar" style="left:222px"><span role="img" aria-label="Client portrait" style="background:linear-gradient(#b9b2a9,#7a6a5e)"></span></div>
  <div class="abs avatar" style="left:561px"><span role="img" aria-label="Client portrait" style="background:linear-gradient(#c9c9c9,#4a4f5a)"></span></div>
  <div class="abs avatar" style="left:900px"><span role="img" aria-label="Client portrait" style="background:linear-gradient(#d8c6b4,#8a6a50)"></span></div>
</section>

<footer>
  <div class="abs site-footer"></div>
  <div class="abs brand brand-footer">Harbourline IT</div>
  <div class="abs social" style="left:114px;background:var(--red);border-color:var(--red)"></div>
  <div class="abs social" style="left:157px"></div>
  <div class="abs social" style="left:196px"></div>

  <div class="abs foot-col" style="left:455px;top:2096px">
    <h4>QUICK LINKS</h4>
    <ul>
      <li><svg width="14" height="12" viewBox="0 0 14 12"><path d="M1 6h10M7 1l5 5-5 5" stroke="#fff" stroke-width="2.2" fill="none"/></svg>Home</li>
      <li><svg width="14" height="12" viewBox="0 0 14 12"><path d="M1 6h10M7 1l5 5-5 5" stroke="#fff" stroke-width="2.2" fill="none"/></svg>Our Services</li>
      <li><svg width="14" height="12" viewBox="0 0 14 12"><path d="M1 6h10M7 1l5 5-5 5" stroke="#fff" stroke-width="2.2" fill="none"/></svg>Our Team</li>
      <li><svg width="14" height="12" viewBox="0 0 14 12"><path d="M1 6h10M7 1l5 5-5 5" stroke="#fff" stroke-width="2.2" fill="none"/></svg>Partners</li>
      <li><svg width="14" height="12" viewBox="0 0 14 12"><path d="M1 6h10M7 1l5 5-5 5" stroke="#fff" stroke-width="2.2" fill="none"/></svg>Contact Us</li>
    </ul>
  </div>
  <div class="abs foot-col" style="left:662px;top:2096px">
    <h4>HELP LINKS</h4>
    <ul>
      <li><svg width="14" height="12" viewBox="0 0 14 12"><path d="M1 6h10M7 1l5 5-5 5" stroke="#fff" stroke-width="2.2" fill="none"/></svg>FAQ</li>
      <li><svg width="14" height="12" viewBox="0 0 14 12"><path d="M1 6h10M7 1l5 5-5 5" stroke="#fff" stroke-width="2.2" fill="none"/></svg>Terms of use</li>
      <li><svg width="14" height="12" viewBox="0 0 14 12"><path d="M1 6h10M7 1l5 5-5 5" stroke="#fff" stroke-width="2.2" fill="none"/></svg>Privacy Policy</li>
      <li><svg width="14" height="12" viewBox="0 0 14 12"><path d="M1 6h10M7 1l5 5-5 5" stroke="#fff" stroke-width="2.2" fill="none"/></svg>Support Links</li>
      <li><svg width="14" height="12" viewBox="0 0 14 12"><path d="M1 6h10M7 1l5 5-5 5" stroke="#fff" stroke-width="2.2" fill="none"/></svg>Conditions</li>
    </ul>
  </div>
  <div class="abs foot-col" style="left:888px;top:2096px">
    <h4>CONTACT US</h4>
    <div class="contact-row" style="margin-top:18px">
      <span class="ic"><svg width="14" height="18" viewBox="0 0 14 18"><path d="M7 0C3 0 0 3 0 7c0 5 7 11 7 11s7-6 7-11c0-4-3-7-7-7z" fill="#111"/><circle cx="7" cy="7" r="2.5" fill="#fff"/></svg></span>
      <span>Harbourline IT<br>Level 4, Harbour St, Sydney</span>
    </div>
    <div class="contact-row" style="margin-top:18px">
      <span class="ic"><svg width="16" height="16" viewBox="0 0 16 16"><path d="M3 1l3 3-2 2c1 2 3 4 5 5l2-2 3 3-2 3C6 15 1 10 0 3z" fill="#111"/></svg></span>
      <span>1300 555 014</span>
    </div>
    <div class="contact-row" style="margin-top:20px">
      <span class="ic"><svg width="16" height="12" viewBox="0 0 16 12"><rect width="16" height="12" rx="2" fill="#111"/><path d="M1 1l7 6 7-6" stroke="#fff" stroke-width="1.4" fill="none"/></svg></span>
      <span>info@harbourlineit.com.au</span>
    </div>
  </div>

  <div class="abs rule"></div>
  <p class="abs copyright">Copyrights@2025.Harbourline IT.All Rights Reserved</p>
</footer>

</body>
</html>
```